Local Roofing/Construction company business needs new biz card design

We need a new business card design, current cards are from the start of this operation and generic at best. We are a local Construction Company (General Contractor) with a majority of our work originating from insurance claims-exterior finish work is the main focus (Roofs-Siding-Gutters etc). Heavily involved with homeowners and the low ball offers they receive from insurance company's after a insurable event takes place. I have attached some of our original logo file(s) below.

```html
<!DOCTYPE html>
<html lang="en">
<head>
<meta charset="utf-8">
<title>Stonegate Exteriors – Business Card</title>
<link href="https://fonts.googleapis.com/css2?family=Open+Sans:wght@400;600;700;800&display=swap" rel="stylesheet">
<style>
  :root {
    --brand-green: #55be6f;
    --deep-teal: #0b1e1f;
    --ink: #061414;
    --white: #ffffff;
    --stage: #1c1c1f;
  }
  * { margin: 0; padding: 0; box-sizing: border-box; }
  html, body { width: 1200px; height: 780px; overflow: hidden; }
  body {
    background: var(--stage);
    font-family: "Open Sans", Arial, sans-serif;
    display: flex;
    align-items: center;
    justify-content: center;
    gap: 40px;
  }
  .card {
    width: 540px;
    height: 309px;
    border-radius: 22px;
    position: relative;
    overflow: hidden;
    box-shadow: 0 18px 40px rgba(0,0,0,.45);
  }

  /* Front */
  .card--front {
    background: var(--brand-green);
    display: flex;
    align-items: center;
    justify-content: center;
  }
  .wordmark-badge {
    background: var(--ink);
    clip-path: polygon(22px 0, 100% 0, 100% calc(100% - 22px), calc(100% - 22px) 100%, 0 100%, 0 22px);
    padding: 26px 36px;
    display: flex;
    align-items: center;
    gap: 16px;
  }
  .wordmark-badge__square {
    width: 30px; height: 30px;
    background: var(--white);
  }
  .wordmark-badge__name {
    color: var(--white);
    font-weight: 800;
    font-size: 30px;
    letter-spacing: 1px;
    text-transform: uppercase;
    line-height: 1.05;
  }

  /* Back */
  .card--back {
    background: var(--deep-teal);
    border: 4px solid var(--brand-green);
  }
  .back-badge {
    position: absolute;
    left: 22px; top: 24px;
    background: var(--brand-green);
    clip-path: polygon(14px 0, 100% 0, 100% calc(100% - 14px), calc(100% - 14px) 100%, 0 100%, 0 14px);
    padding: 12px 20px;
    display: flex;
    align-items: center;
    gap: 10px;
  }
  .back-badge__square { width: 16px; height: 16px; background: var(--white); }
  .back-badge__name {
    color: var(--white);
    font-weight: 800;
    font-size: 17px;
    letter-spacing: .6px;
    text-transform: uppercase;
  }
  .contact {
    position: absolute;
    left: 26px; top: 96px;
    color: var(--white);
  }
  .contact__name {
    color: var(--brand-green);
    font-weight: 700;
    font-size: 24px;
    line-height: 1.1;
  }
  .contact__role { font-size: 13px; margin-top: 2px; }
  .contact__address { font-size: 12px; line-height: 1.4; margin-top: 12px; }
  .contact__lines { list-style: none; margin-top: 12px; font-size: 12px; line-height: 1.55; }
  .contact__lines li { display: flex; align-items: center; gap: 8px; }
  .contact__lines svg { width: 12px; height: 12px; flex: none; }

  .signature {
    position: absolute;
    right: 0; top: 58px;
    display: flex;
    align-items: stretch;
    gap: 12px;
  }
  .signature__text { text-align: right; padding-top: 2px; }
  .signature__name { font-weight: 700; font-size: 22px; line-height: 1.1; }
  .signature__first { color: var(--brand-green); }
  .signature__last { color: var(--white); }
  .signature__role { color: var(--white); font-size: 12px; margin-top: 2px; }
  .signature__bar { width: 14px; background: var(--brand-green); }
</style>
</head>
<body>

  <section class="card card--front" aria-label="Card front">
    <div class="wordmark-badge">
      <span class="wordmark-badge__square"></span>
      <span class="wordmark-badge__name">Stonegate<br>Exteriors</span>
    </div>
  </section>

  <section class="card card--back" aria-label="Card back">
    <div class="back-badge">
      <span class="back-badge__square"></span>
      <span class="back-badge__name">Stonegate Exteriors</span>
    </div>

    <div class="signature">
      <div class="signature__text">
        <div class="signature__name"><span class="signature__first">Marta</span> <span class="signature__last">Holloway</span></div>
        <div class="signature__role">Managing Director</div>
      </div>
      <div class="signature__bar"></div>
    </div>

    <div class="contact">
      <div class="contact__name">Marta Holloway</div>
      <div class="contact__role">Co-Founder</div>
      <div class="contact__address">42 Cedar Hollow<br>Dr, Fairview, MO 63000</div>
      <ul class="contact__lines">
        <li>
          <svg viewBox="0 0 24 24" aria-hidden="true"><path fill="#55be6f" d="M6.6 10.8a15 15 0 0 0 6.6 6.6l2.2-2.2a1 1 0 0 1 1-.25 11.4 11.4 0 0 0 3.6.57 1 1 0 0 1 1 1V20a1 1 0 0 1-1 1A17 17 0 0 1 3 4a1 1 0 0 1 1-1h3.5a1 1 0 0 1 1 1c0 1.25.2 2.45.57 3.57a1 1 0 0 1-.25 1z"/></svg>
          555-201-4410
        </li>
        <li>
          <svg viewBox="0 0 24 24" aria-hidden="true"><path fill="#55be6f" d="M6.6 10.8a15 15 0 0 0 6.6 6.6l2.2-2.2a1 1 0 0 1 1-.25 11.4 11.4 0 0 0 3.6.57 1 1 0 0 1 1 1V20a1 1 0 0 1-1 1A17 17 0 0 1 3 4a1 1 0 0 1 1-1h3.5a1 1 0 0 1 1 1c0 1.25.2 2.45.57 3.57a1 1 0 0 1-.25 1z"/></svg>
          555-201-7730 (Emergency)
        </li>
        <li>
          <svg viewBox="0 0 24 24" aria-hidden="true"><circle cx="12" cy="12" r="9" fill="none" stroke="#55be6f" stroke-width="2"/><path d="M3 12h18M12 3c3 3 3 15 0 18M12 3c-3 3-3 15 0 18" fill="none" stroke="#55be6f" stroke-width="1.6"/></svg>
          www.stonegateexteriors.com
        </li>
        <li>
          <svg viewBox="0 0 24 24" aria-hidden="true"><rect x="3" y="6" width="18" height="13" rx="1.5" fill="#55be6f"/><path d="M3.5 7l8.5 6.5L20.5 7" fill="none" stroke="#0b1e1f" stroke-width="1.6"/></svg>
          office@stonegateexteriors.com
        </li>
      </ul>
    </div>
  </section>

</body>
</html>
```